VOMRA Pty Ltd Business Card

Looking for a simple yet eye-catching double-sided business card design using my company logo on one side and contact details on the other.

Target Market(s)

Government

Industry/Entity Type

Communication Systems Engineering

Contact Information for Business Card

VOMRA Pty Ltd

Requirements
Nice to have
• Would be great to have a QR code so details can be scanned into contacts

```html
<!DOCTYPE html>
<html lang="en">
<head>
<meta charset="utf-8">
<title>VOMRA Pty Ltd Business Card</title>
<link href="https://fonts.googleapis.com/css2?family=Montserrat:wght@400;700&display=swap" rel="stylesheet">
<style>
  :root {
    --page: #e4e6e8;
    --card: #ffffff;
    --slate: #36414a;
    --ink: #111417;
    --text: #2c353c;
  }
  html, body {
    margin: 0;
    padding: 0;
    width: 1200px;
    height: 960px;
    overflow: hidden;
    background: var(--page);
    font-family: "Montserrat", Arial, sans-serif;
  }
  .card {
    position: absolute;
    left: 250px;
    width: 700px;
    height: 400px;
    background: var(--card);
    border-radius: 26px;
    overflow: hidden;
    box-shadow: 0 6px 18px rgba(0,0,0,0.12);
  }
  .card--front { top: 50px; }
  .card--back { top: 510px; }

  .brand {
    position: absolute;
    display: flex;
    align-items: center;
    color: var(--slate);
    font-weight: 700;
    letter-spacing: 2px;
  }
  .brand__dot {
    border-radius: 50%;
    background: var(--slate);
  }
  .card--front .brand {
    left: 120px;
    top: 150px;
    gap: 34px;
    font-size: 92px;
    line-height: 1;
  }
  .card--front .brand__dot { width: 90px; height: 90px; }

  .card--back .brand {
    left: 62px;
    top: 166px;
    gap: 18px;
    font-size: 48px;
    line-height: 1;
  }
  .card--back .brand__dot { width: 48px; height: 48px; }

  .divider {
    position: absolute;
    left: 392px;
    top: 62px;
    width: 2px;
    height: 190px;
    background: var(--slate);
  }
  .contact {
    position: absolute;
    left: 418px;
    top: 60px;
    color: var(--text);
  }
  .contact__name {
    margin: 0;
    font-size: 22px;
    font-weight: 700;
    color: var(--slate);
    letter-spacing: 0.5px;
  }
  .contact__role {
    margin: 2px 0 18px;
    font-size: 14px;
  }
  .contact__list {
    list-style: none;
    margin: 0 0 16px;
    padding: 0;
    font-size: 14px;
  }
  .contact__list li {
    display: flex;
    align-items: center;
    gap: 8px;
    margin-bottom: 4px;
  }
  .contact__list svg { width: 13px; height: 13px; fill: var(--slate); }
  .contact__address {
    margin: 0;
    font-size: 14px;
    line-height: 1.35;
    font-style: normal;
  }
  .swoosh {
    position: absolute;
    left: 0;
    top: 0;
    width: 700px;
    height: 400px;
  }
</style>
</head>
<body>

<section class="card card--front" aria-label="Business card front">
  <div class="brand"><span class="brand__dot"></span>VOMRA</div>
</section>

<section class="card card--back" aria-label="Business card back">
  <svg class="swoosh" viewBox="0 0 700 400" aria-hidden="true">
    <path fill="var(--slate)" d="M150,400 Q360,260 700,232 L700,250 Q420,290 260,400 Z"/>
    <path fill="var(--ink)" d="M262,400 Q430,292 700,258 L700,266 Q440,302 285,400 Z"/>
    <path fill="var(--slate)" d="M300,400 Q460,310 700,278 L700,400 Z"/>
  </svg>

  <div class="brand"><span class="brand__dot"></span>VOMRA</div>

  <div class="divider"></div>

  <div class="contact">
    <h1 class="contact__name">DANIEL HARTLEY</h1>
    <p class="contact__role">Managing Director</p>
    <ul class="contact__list">
      <li>
        <svg viewBox="0 0 24 24" aria-hidden="true"><path d="M6.6 10.8a15 15 0 0 0 6.6 6.6l2.2-2.2c.3-.3.7-.4 1-.2 1.1.4 2.3.6 3.6.6.6 0 1 .4 1 1V20c0 .6-.4 1-1 1A17 17 0 0 1 3 4c0-.6.4-1 1-1h3.5c.6 0 1 .4 1 1 0 1.3.2 2.5.6 3.6.1.3 0 .7-.2 1z"/></svg>
        987 654 321
      </li>
      <li>
        <svg viewBox="0 0 24 24" aria-hidden="true"><path d="M2 5h20v14H2z M2 5l10 8 10-8" /></svg>
        admin@vomra.com.au
      </li>
      <li>
        <svg viewBox="0 0 24 24" aria-hidden="true"><circle cx="12" cy="12" r="10"/></svg>
        www.vomra.com.au
      </li>
    </ul>
    <address class="contact__address">45-47 Harlow Street Ashfield<br>Vale NSW 2150 Australia</address>
  </div>
</section>

</body>
</html>
```